Stylish business cards for KV7

To create an appealing and professional business card design for a WOMEN Owned Construction Supply Company.
2 sided card. Incorporate brand elements, curvy, colorful, sleek and bright. No solid white background. attached samples of styles added shapes/ribbons. Want something with that WOW that looks awesome, factor. It is a new logo, so feel free to mess with logo colors in the blue and teal factors that can look good with both dark and light background. If you want to try a watermark with just the KV7, without the "Supply" that might look cool to.

Industry/Entity Type

Women owned construction supply company

Contact Information for Business Card

Name, Title, and phone number and email, web page. maybe spot for qr code.

Font styles to use
Sans Serif

Requirements
Nice to have
• would love to see colors, maybe stylish ribbon dividers or some sort of 2 or 3 tone color card that compliments logo.
Should not have
• Please do not have all white background. Do not include Home/reale state/ or building images.

```html
<!DOCTYPE html>
<html lang="en">
<head>
<meta charset="utf-8">
<title>KV7 Supply – Business Cards</title>
<link href="https://fonts.googleapis.com/css2?family=Nunito+Sans:wght@400;600;700;800&display=swap" rel="stylesheet">
<style>
  :root {
    --backdrop: #1f1f20;
    --navy: #1b3a5c;
    --teal: #2393ba;
    --paper: #f3f4f5;
    --white: #ffffff;
    --font: "Nunito Sans", Arial, sans-serif;
  }
  * { margin: 0; padding: 0; box-sizing: border-box; }
  html, body {
    width: 1200px; height: 1059px; overflow: hidden;
    background: var(--backdrop);
    font-family: var(--font);
  }
  .canvas { position: relative; width: 1200px; height: 1059px; }

  .card {
    position: absolute;
    border-radius: 18px;
    overflow: hidden;
    box-shadow: 0 10px 24px rgba(0,0,0,.45);
  }
  .card-front { left: 257px; top: 89px; width: 687px; height: 390px; background: var(--paper); }
  .card-back  { left: 254px; top: 546px; width: 693px; height: 393px; background: var(--navy); }

  .divider-bands { position: absolute; inset: 0; width: 100%; height: 100%; }

  .brand-name {
    position: absolute;
    font-family: var(--font);
    font-weight: 800;
    white-space: nowrap;
    letter-spacing: 0.5px;
  }
  .card-front .brand-name { left: 400px; top: 82px; font-size: 38px; color: var(--navy); }

  .holder { position: absolute; left: 34px; top: 218px; color: var(--white); }
  .holder-name { font-size: 24px; font-weight: 800; color: var(--teal); letter-spacing: 0.4px; line-height: 1; }
  .holder-title { font-size: 16px; font-weight: 400; margin-top: 4px; }
  .holder-rule { width: 12px; height: 1px; background: var(--teal); margin-top: 11px; }

  .contacts { position: absolute; left: 34px; top: 278px; list-style: none; color: var(--white); }
  .contacts li { display: flex; align-items: center; font-size: 16.5px; height: 27px; }
  .contacts svg { width: 13px; height: 13px; margin-right: 8px; fill: var(--teal); flex: none; }

  .address {
    position: absolute; right: 34px; top: 312px;
    font-style: normal;
    text-align: right; color: var(--white); font-size: 16.5px; line-height: 22px;
  }

  .watermark {
    position: absolute; left: 0; top: 70px;
    font-weight: 800; font-size: 300px; line-height: 1;
    color: rgba(255,255,255,.05);
  }
  .card-back .brand-name { left: 0; right: 0; top: 160px; text-align: center; font-size: 66px; color: var(--white); }
</style>
</head>
<body>
<main class="canvas">

  <section class="card card-front" aria-label="Business card front">
    <svg class="divider-bands" viewBox="0 0 687 390" preserveAspectRatio="none" aria-hidden="true">
      <path d="M0,24 C200,130 430,205 687,166 L687,390 L0,390 Z" fill="var(--navy)"/>
      <path d="M0,58 C200,160 450,225 687,186 L687,196 C450,238 200,172 0,66 Z" fill="var(--white)"/>
      <path d="M0,70 C200,178 450,246 687,198 L687,222 C470,280 220,228 0,100 Z" fill="var(--teal)"/>
    </svg>
    <div class="brand-name">KV7 Supply</div>

    <div class="holder">
      <h1 class="holder-name">DELIA MARSH</h1>
      <p class="holder-title">CEO/Founder</p>
      <div class="holder-rule"></div>
    </div>

    <ul class="contacts">
      <li><svg viewBox="0 0 24 24"><path d="M6.6 10.8a15.1 15.1 0 0 0 6.6 6.6l2.2-2.2a1 1 0 0 1 1-.25 11.4 11.4 0 0 0 3.6.57 1 1 0 0 1 1 1V20a1 1 0 0 1-1 1A17 17 0 0 1 3 4a1 1 0 0 1 1-1h3.5a1 1 0 0 1 1 1c0 1.25.2 2.45.57 3.57a1 1 0 0 1-.25 1z"/></svg>555.014.2290</li>
      <li><svg viewBox="0 0 24 24"><path d="M2 5h20v14H2z M3.5 6.5 12 13l8.5-6.5" fill="var(--teal)" stroke="var(--navy)" stroke-width="1.5"/></svg>info@kv7supply.com.au</li>
      <li><svg viewBox="0 0 24 24"><circle cx="12" cy="12" r="9.5" fill="none" stroke="var(--teal)" stroke-width="2"/><path d="M2.5 12h19M12 2.5c3 3 3 16 0 19M12 2.5c-3 3-3 16 0 19" fill="none" stroke="var(--teal)" stroke-width="1.6"/></svg>www.kv7supply.com.au</li>
    </ul>

    <address class="address">
      P.O Box 3170 Harbour Lane<br>
      Westvale AB 40215
    </address>
  </section>

  <section class="card card-back" aria-label="Business card back">
    <div class="watermark" aria-hidden="true">KV7</div>
    <div class="brand-name">KV7 Supply</div>
  </section>

</main>
</body>
</html>
```